Veterinary Pylon

My veterinary clinic is not clearly visible from the street and I want to place a Pylon next to my driveway. I want a modern, elegant straight Design, the Photo shows the sheduled place. One can see the clinic on our Homepage: www.tailbright-vethaus.at
The last pictures are examples for pylones I like

Target Market(s)

the passing cars often miss my entry...I want to show where to turn left

Colors
3276b5
33a6d7
00a990

Requirements
Must have
• High value, simple elegance, size: 250cm (high) x 100cm (width)
Nice to have
• Our Logo, arrow(?)

A special Text is not necessary but this will be an option:

Biegen sie hier ab und wir biegen es wieder hin!
Should not have
• Too much Color, the colors I have chosen are the possible colors but it‘s not necessary to use them.

```html
<!DOCTYPE html>
<html lang="de">
<head>
<meta charset="utf-8">
<title>Tailbright Vethaus – Pylon</title>
<link rel="stylesheet" href="https://fonts.googleapis.com/css2?family=Archivo+Black&display=swap">
<style>
  :root {
    --navy: #114a93;
    --blue: #2387cc;
    --cyan: #2cb8dc;
    --aqua: #57e1f0;
    --mist: #e7f1f8;
    --mist-cyan: #ecf9fb;
    --white: #ffffff;
  }
  html, body {
    margin: 0;
    padding: 0;
    width: 1200px;
    height: 3000px;
    overflow: hidden;
    background: var(--white);
  }
  .pylon {
    position: relative;
    width: 1200px;
    height: 3000px;
    overflow: hidden;
    background: var(--white);
  }
  .pylon__waves {
    position: absolute;
    inset: 0;
    width: 1200px;
    height: 3000px;
  }
  .brand__mark {
    position: absolute;
    left: 420px;
    top: 180px;
    width: 360px;
    height: 360px;
    border-radius: 50%;
    background: var(--cyan);
  }
  .brand__name {
    position: absolute;
    left: 0;
    right: 0;
    top: 740px;
    margin: 0;
    font-family: "Archivo Black", sans-serif;
    font-weight: 400;
    color: var(--navy);
    font-size: 150px;
    line-height: 1.2;
    letter-spacing: 0;
    text-align: center;
    text-transform: uppercase;
  }
  .turn-arrow {
    position: absolute;
    left: 413px;
    top: 1318px;
    width: 434px;
    height: 434px;
  }
  .footer-mark {
    position: absolute;
    left: 0;
    right: 0;
    top: 2440px;
    display: flex;
    flex-direction: column;
    align-items: center;
  }
  .footer-mark__dot {
    width: 190px;
    height: 190px;
    border-radius: 50%;
    background: var(--navy);
    margin-bottom: 50px;
  }
  .footer-mark__name {
    margin: 0;
    font-family: "Archivo Black", sans-serif;
    font-weight: 400;
    color: var(--navy);
    font-size: 132px;
    line-height: 1.15;
    text-align: center;
    text-transform: uppercase;
  }
</style>
</head>
<body>
<main class="pylon">
  <svg class="pylon__waves" viewBox="0 0 1030 2576" preserveAspectRatio="none" aria-hidden="true">
    <path d="M0,1695 C200,1660 400,1680 570,1745 C780,1830 930,1960 1030,2100 L1030,2576 L0,2576 Z" fill="var(--mist)"/>
    <path d="M570,1745 C720,1685 880,1670 1030,1685 L1030,2100 C930,1960 780,1830 570,1745 Z" fill="var(--mist-cyan)"/>
    <path d="M560,1700 C720,1625 880,1615 1030,1636 L1030,1672 C880,1655 720,1670 572,1732 Z" fill="var(--aqua)"/>
    <path d="M0,1643 C200,1600 420,1625 612,1712 L570,1730 C390,1665 200,1650 0,1682 Z" fill="var(--blue)"/>
  </svg>

  <header class="brand">
    <div class="brand__mark"></div>
    <h1 class="brand__name">Tailbright<br>Vethaus</h1>
  </header>

  <svg class="turn-arrow" viewBox="0 0 372 372" role="img" aria-label="Pfeil nach links – hier abbiegen">
    <defs>
      <linearGradient id="arrowFill" x1="0" y1="0" x2="1" y2="0">
        <stop offset="0" stop-color="#114a93"/>
        <stop offset="1" stop-color="#2cb8dc"/>
      </linearGradient>
    </defs>
    <circle cx="186" cy="186" r="186" fill="url(#arrowFill)"/>
    <path d="M162,101 L162,131 L112,180 L295,180 L295,198 L112,198 L162,247 L162,271 L77,186 Z" fill="#ffffff"/>
  </svg>

  <footer class="footer-mark">
    <div class="footer-mark__dot"></div>
    <p class="footer-mark__name">Tailbright<br>Vethaus</p>
  </footer>
</main>
</body>
</html>
```